Quorvane Systems
Business Cards
Quorvane Systems - Information Technology
Creative Brief
Professional
Malcolm Treadby
Vice President
Quorvane IT Systems Harrowgate Tower 418 Pellham Ave North,Suite 2700 Toronto ON, M4R 2K7
malcolm.treadby@quorvanesystems.example
www.quorvanesystems.example

```html
<!DOCTYPE html>
<html lang="en">
<head>
<meta charset="utf-8">
<title>Quorvane Systems Stationery Concepts</title>
<link rel="stylesheet" href="https://fonts.googleapis.com/css2?family=Open+Sans:wght@400;700&display=swap">
<style>
:root{
  --bg:#2a2a2c;
  --bg-line:#323235;
  --paper:#ffffff;
  --paper-shade:#eef1f3;
  --blue:#1c9bd7;
  --blue-dark:#0b6ea6;
  --blue-pale:#d7ecf7;
  --ink:#3b3e42;
  --ink-soft:#8a8e93;
  --env-grey:#5d6064;
  --label:#c9cbce;
}
*{margin:0;padding:0;box-sizing:border-box}
html,body{width:1200px;height:382px;overflow:hidden;background:var(--bg)}
body{font-family:"Open Sans",Arial,sans-serif;position:relative;
  background-image:repeating-linear-gradient(45deg,var(--bg-line) 0 1px,transparent 1px 6px)}
.board{position:relative;width:1200px;height:382px}
.abs{position:absolute}

.brand{left:20px;top:18px;display:flex;align-items:center;gap:8px}
.brand-dot{width:34px;height:34px;border-radius:50%;background:var(--blue)}
.brand-name{color:var(--paper);font-weight:700;font-size:15px;line-height:1.05;text-transform:uppercase;width:140px}
.board-title{left:22px;top:86px;color:var(--label);font-size:10px}

.label{color:var(--label);font-size:5.5px;text-align:center}

.card{width:132px;height:65px;background:var(--paper);overflow:hidden;border-radius:2px}
.card svg{position:absolute;left:0;bottom:0}
.mini-brand{display:flex;align-items:center;gap:3px}
.mini-dot{width:10px;height:10px;background:var(--blue);border-radius:2px}
.mini-name{font-weight:700;font-size:5px;color:var(--blue-dark);text-transform:uppercase;line-height:1.1;width:44px}
.card-info{font-size:3.4px;color:var(--ink);line-height:1.45}
.card-info b{font-size:4.5px;color:var(--blue-dark)}
.card--blue{background:linear-gradient(160deg,var(--blue) 0%,var(--blue-dark) 100%)}
.card--blue .mini-dot{background:var(--paper)}
.card--blue .mini-name{color:var(--paper)}

.sheet{width:168px;height:341px;background:var(--paper);overflow:hidden}
.sheet .mark{position:absolute;left:44px;top:110px;width:80px;height:80px;border-radius:50%;background:var(--blue-pale);opacity:.55}
.sheet svg{position:absolute;left:0;bottom:0}
.sheet-contact{position:absolute;right:10px;top:12px;font-size:3px;color:var(--ink-soft);line-height:1.5;text-align:right}

.envelope{width:206px;overflow:hidden;background:var(--paper);border-radius:1px}
.envelope svg{display:block}
</style>
</head>
<body>
<main class="board">

  <header class="brand abs">
    <span class="brand-dot"></span>
    <span class="brand-name">Quorvane IT Systems</span>
  </header>
  <p class="board-title abs">Stationery Concepts</p>

  <!-- business cards -->
  <section class="card abs" style="left:19px;top:144px">
    <div class="mini-brand abs" style="left:10px;top:12px"><span class="mini-dot"></span><span class="mini-name">Quorvane IT Systems</span></div>
    <svg width="132" height="24" viewBox="0 0 132 24"><path d="M0 14 C40 4 90 22 132 8 V24 H0Z" fill="var(--blue)"/></svg>
  </section>
  <p class="label abs" style="left:19px;top:214px;width:132px">Front Card 01</p>

  <section class="card abs" style="left:161px;top:144px">
    <div class="mini-brand abs" style="left:8px;top:8px"><span class="mini-dot"></span><span class="mini-name">Quorvane IT Systems</span></div>
    <div class="card-info abs" style="left:70px;top:12px">
      <b>Malcolm Treadby</b><br>Vice President<br>Harrowgate Tower<br>418 Pellham Ave North,Suite 2700<br>Toronto ON, M4R 2K7<br>+1 416 555 0142<br>malcolm.treadby@quorvanesystems.example<br>www.quorvanesystems.example
    </div>
    <svg width="132" height="8" viewBox="0 0 132 8"><rect y="5" width="132" height="3" fill="var(--blue)"/></svg>
  </section>
  <p class="label abs" style="left:161px;top:214px;width:158px">Back Card 01</p>

  <section class="card card--blue abs" style="left:19px;top:240px">
    <div class="mini-brand abs" style="left:10px;top:12px"><span class="mini-dot"></span><span class="mini-name">Quorvane IT Systems</span></div>
  </section>
  <p class="label abs" style="left:19px;top:311px;width:132px">Front Card 02</p>

  <section class="card abs" style="left:161px;top:240px">
    <div class="mini-brand abs" style="left:8px;top:8px"><span class="mini-dot"></span><span class="mini-name">Quorvane IT Systems</span></div>
    <div class="card-info abs" style="left:70px;top:12px">
      <b>Malcolm Treadby</b><br>Vice President<br>Harrowgate Tower<br>418 Pellham Ave North,Suite 2700<br>Toronto ON, M4R 2K7<br>+1 416 555 0142<br>malcolm.treadby@quorvanesystems.example<br>www.quorvanesystems.example
    </div>
    <svg width="132" height="20" viewBox="0 0 132 20"><path d="M0 12 C40 20 90 4 132 14 V20 H0Z" fill="var(--blue)"/></svg>
  </section>
  <p class="label abs" style="left:161px;top:311px;width:158px">Back Card 02</p>

  <!-- letterheads -->
  <section class="sheet abs" style="left:341px;top:18px">
    <div class="mini-brand abs" style="left:10px;top:10px"><span class="mini-dot"></span><span class="mini-name">Quorvane IT Systems</span></div>
    <div class="sheet-contact">Harrowgate Tower<br>418 Pellham Ave North,Suite 2700<br>Toronto ON, M4R 2K7<br>www.quorvanesystems.example</div>
    <span class="mark"></span>
    <svg width="168" height="40" viewBox="0 0 168 40">
      <path d="M0 20 C50 8 110 32 168 14 V40 H0Z" fill="var(--blue)"/>
      <path d="M0 28 C60 18 110 38 168 26 V40 H0Z" fill="var(--blue-dark)"/>
    </svg>
  </section>
  <p class="label abs" style="left:341px;top:364px;width:168px">Letterhead 01</p>

  <section class="sheet abs" style="left:521px;top:18px">
    <div class="mini-brand abs" style="left:10px;top:10px"><span class="mini-dot"></span><span class="mini-name">Quorvane IT Systems</span></div>
    <div class="sheet-contact">Harrowgate Tower<br>418 Pellham Ave North,Suite 2700<br>Toronto ON, M4R 2K7<br>www.quorvanesystems.example</div>
    <span class="mark"></span>
    <svg width="168" height="30" viewBox="0 0 168 30">
      <path d="M0 18 C60 10 110 26 168 12 V30 H0Z" fill="var(--blue)"/>
    </svg>
  </section>
  <p class="label abs" style="left:521px;top:364px;width:168px">Letterhead 02</p>

  <!-- envelopes -->
  <section class="envelope abs" style="left:713px;top:22px;height:78px;background:var(--env-grey)">
    <svg width="206" height="78" viewBox="0 0 206 78"><path d="M0 0 L103 40 L206 0Z" fill="#4b4e52"/><rect x="98" y="30" width="10" height="10" rx="2" fill="var(--paper)"/></svg>
  </section>
  <section class="envelope abs" style="left:713px;top:106px;height:62px">
    <svg width="206" height="62" viewBox="0 0 206 62"><path d="M0 0 L103 32 L206 0Z" fill="var(--env-grey)"/><rect x="98" y="22" width="10" height="10" rx="2" fill="var(--paper)"/></svg>
  </section>
  <section class="envelope abs" style="left:713px;top:170px;height:64px;background:var(--paper-shade)">
    <svg width="206" height="64" viewBox="0 0 206 64"><path d="M0 0 L103 30 L206 0Z" fill="var(--blue)"/><rect x="98" y="20" width="10" height="10" rx="2" fill="var(--paper)"/></svg>
  </section>
  <section class="envelope abs" style="left:713px;top:244px;height:96px">
    <div class="mini-brand abs" style="left:10px;top:10px"><span class="mini-dot"></span><span class="mini-name">Quorvane IT Systems</span></div>
    <div class="sheet-contact" style="left:10px;right:auto;top:26px;text-align:left">Harrowgate Tower<br>418 Pellham Ave North,Suite 2700<br>Toronto ON, M4R 2K7</div>
    <svg class="abs" style="left:0;bottom:0" width="206" height="22" viewBox="0 0 206 22">
      <path d="M0 12 C70 2 140 20 206 6 V22 H0Z" fill="var(--blue)"/>
    </svg>
  </section>
  <p class="label abs" style="left:713px;top:348px;width:206px">Envelope Set</p>

</main>
</body>
</html>
```